Local fast-growing company in the service sector

We are looking for a modern business card design, which should also appear on our letterheads

Target Market(s)

Private and industrial sectors

Contact Information for Business Card

Vorname Name
Kellberger Str. 18
73614 Lindenhain
Tel.: 07146-839214-0
Name@agentur-kvtl.de

Colors
9d9d9d
919191
aaaaaa

Requirements
Must have
• The logo (file) in silver

```html
<!DOCTYPE html>
<html lang="de">
<head>
<meta charset="utf-8">
<title>KVTL – Visitenkarte</title>
<link rel="stylesheet" href="https://fonts.googleapis.com/css2?family=Roboto:wght@400;500;700&display=swap">
<style>
  :root {
    --bg: #e8e5e1;
    --card-light: #f7f7f7;
    --card-dark: #1c1d1e;
    --panel: #ffffff;
    --silver: #9d9d9d;
    --silver-mid: #919191;
    --silver-light: #aaaaaa;
    --text-dark: #3f3f3f;
    --text-muted: #5a5a5a;
  }
  * { margin: 0; padding: 0; box-sizing: border-box; }
  html, body {
    width: 1200px; height: 960px; overflow: hidden;
    background: var(--bg);
    font-family: "Roboto", sans-serif;
  }
  .stage { position: relative; width: 1200px; height: 960px; }

  .card {
    position: absolute;
    border-radius: 22px;
    overflow: hidden;
  }
  .card--front {
    left: 320px; top: 96px; width: 604px; height: 352px;
    background: var(--card-light);
    box-shadow: 0 2px 6px rgba(0,0,0,.12);
  }
  .card--back {
    left: 320px; top: 493px; width: 598px; height: 342px;
    background: var(--card-dark);
    box-shadow: 0 2px 6px rgba(0,0,0,.25);
  }

  .wordmark {
    position: absolute;
    display: flex; align-items: center; gap: 14px;
    font-weight: 700; letter-spacing: 1px;
    white-space: nowrap;
  }
  .wordmark__dot {
    display: block; width: 0.7em; height: 0.7em;
    background: currentColor;
  }
  .card--front .wordmark {
    left: 0; right: 0; justify-content: center;
    top: 146px; font-size: 64px; color: var(--silver);
  }
  .card--front .site {
    position: absolute; left: 0; right: 0; top: 298px;
    text-align: center; font-size: 15px; letter-spacing: 6.5px;
    color: var(--text-muted);
  }

  .contact-panel {
    position: absolute; left: 10px; top: 0; width: 298px; height: 340px;
    background: var(--panel);
    border-radius: 20px;
  }
  .contact-panel__name {
    position: absolute; left: 0; right: 0; top: 102px;
    text-align: center; font-size: 20px; font-weight: 500;
    color: #7b7b7b;
  }
  .contact-list {
    position: absolute; left: 27px; top: 184px;
    list-style: none; font-size: 14px; color: var(--text-dark);
  }
  .contact-list li {
    display: flex; align-items: center; gap: 9px;
    height: 19.5px;
  }
  .contact-list svg { width: 13px; height: 13px; fill: #555; flex: none; }
  .contact-panel__address {
    position: absolute; left: 26px; top: 256px;
    font-size: 14px; color: var(--text-dark);
    white-space: nowrap;
  }
  .card--back .wordmark {
    left: 352px; top: 146px; font-size: 48px; color: var(--silver-light);
  }
</style>
</head>
<body>
<main class="stage">

  <section class="card card--front" aria-label="Vorderseite">
    <div class="wordmark"><span class="wordmark__dot"></span>KVTL</div>
    <p class="site">www.agentur-kvtl.de</p>
  </section>

  <section class="card card--back" aria-label="Rückseite">
    <div class="contact-panel">
      <h1 class="contact-panel__name">JONAS WEBER</h1>
      <ul class="contact-list">
        <li>
          <svg viewBox="0 0 16 16" aria-hidden="true"><path d="M3.6 1.2 6 3.6 4.7 5.6c.8 1.9 2.2 3.3 4 4.1l2-1.3 2.4 2.4-1.4 2.3C6.4 13.1 2.9 9.6 1.3 2.6z"/></svg>
          07146-839214-0
        </li>
        <li>
          <svg viewBox="0 0 16 16" aria-hidden="true"><path d="M1 3h14v10H1zM2.2 4.2 8 8.6l5.8-4.4z"/></svg>
          jonas@agentur-kvtl.de
        </li>
        <li>
          <svg viewBox="0 0 16 16" aria-hidden="true"><circle cx="8" cy="8" r="7"/><circle cx="8" cy="8" r="3" fill="#fff"/></svg>
          www.agentur-kvtl.de
        </li>
      </ul>
      <p class="contact-panel__address">Kellberger Str. 18, 73614 Lindenhain</p>
    </div>
    <div class="wordmark"><span class="wordmark__dot"></span>KVTL</div>
  </section>

</main>
</body>
</html>
```